Commercial, Public Works, Contractor needs a modern web design

We are a General and Engineering contracting firm with vast experience in our industry. Our focus is on Commercial, Tenant Improvement, Restaurants, and Public Works. We are opening a new business and would like that excitement and energy to show through the new web design. The colors we like are black, red and grey, we are open to color ideas. Attached is our logo design.

Industry/Entity Type

Restaurant

```html
<!DOCTYPE html>
<html lang="en">
<head>
<meta charset="utf-8">
<title>Redline Builders, Inc. — General Contractor and Engineer</title>
<link rel="stylesheet" href="https://fonts.googleapis.com/css2?family=Open+Sans:wght@400;600;700&family=Titillium+Web:wght@400;600&display=swap">
<style>
:root{
  --red:#b20d12;
  --red-dark:#8e0a0e;
  --ink:#222;
  --text:#555;
  --muted:#777;
  --page:#f3f3f3;
  --card:#fbfbfb;
  --line:#dedede;
  --black:#0c0c0c;
  --white:#fff;
}
*{box-sizing:border-box;margin:0;padding:0}
html,body{width:1200px;height:2387px;overflow:hidden}
body{position:relative;background:var(--page);font-family:"Open Sans",Arial,sans-serif;color:var(--text)}
.abs{position:absolute}
.top-bar{left:0;top:0;width:1200px;height:8px;background:var(--red)}

.brand{left:115px;top:44px;display:flex;align-items:center;gap:10px}
.brand-mark{width:44px;height:44px;border-radius:50%;background:var(--red)}
.brand-text{font-family:"Titillium Web",sans-serif;font-weight:600;color:var(--red);font-size:21px;line-height:1.05}
.brand-text small{display:block;font-size:10px;letter-spacing:.4px;text-transform:uppercase}

.search{left:861px;top:45px;width:224px;height:39px;background:var(--white);border:1px solid var(--line);font-size:12px;color:#888;padding:0 14px;display:flex;align-items:center;justify-content:space-between}

.main-nav{left:115px;top:129px;width:970px;height:86px;background:var(--red);border-radius:4px;overflow:hidden;display:flex}
.main-nav a{color:var(--white);text-decoration:none;font-size:13.5px;font-weight:600;display:flex;align-items:center;justify-content:center;height:100%}
.main-nav a.active{background:var(--black);width:156px}
.main-nav a:not(.active){flex:1}

.slider{left:115px;top:229px;width:970px;height:506px;background:var(--white);border:1px solid var(--line);box-shadow:0 4px 6px rgba(0,0,0,.18)}
.slider-shadow{left:200px;top:735px;width:800px;height:18px;background:radial-gradient(ellipse at top,rgba(0,0,0,.18),rgba(0,0,0,0) 70%)}
.slide{left:9px;top:10px;width:952px;height:486px;background:linear-gradient(135deg,#c9b79a 0%,#e6ddd0 35%,#4f6c93 60%,#2a3d66 100%)}
.slider-arrow{width:32px;height:32px;border-radius:50%;background:#f1f1f1;box-shadow:0 1px 3px rgba(0,0,0,.35);top:232px}
.slider-dots{left:418px;top:472px;width:134px;height:25px;background:var(--white);border-radius:14px 14px 0 0;display:flex;justify-content:center;align-items:center;gap:8px}
.slider-dots span{width:11px;height:11px;border-radius:50%;border:1.5px solid #8aa0c2;background:#eef2f8}
.slider-dots span.on{background:var(--red-dark);border-color:var(--red-dark)}

.section-title{font-family:"Titillium Web",sans-serif;font-weight:400;color:var(--red);font-size:31px;line-height:1}
.welcome-text{left:115px;top:847px;width:615px;font-size:12px;line-height:23.5px;color:var(--text)}
.read-more{left:115px;top:1013px;font-size:12px;color:var(--red-dark)}
.photo-frame{background:var(--white);border:1px solid var(--line);padding:6px}
.photo-fill{width:100%;height:100%}

.service-card{width:228px;height:305px;top:1154px;background:var(--card);border:1px solid var(--line);border-top:3px solid var(--red)}
.service-img{height:167px}
.service-card h3{font-family:"Open Sans",sans-serif;font-weight:600;font-size:16px;color:var(--ink);margin:17px 0 0 10px}
.service-card p{font-size:11.5px;line-height:17px;color:var(--muted);margin:5px 10px 0 10px}
.service-card .more{position:absolute;right:12px;bottom:18px;font-size:11.5px;font-style:italic;color:var(--red-dark)}

.plans{left:115px;top:1515px;width:969px;height:231px;background:linear-gradient(90deg,#7fb1cc 0%,#6ea7c5 45%,#5f9cbd 100%)}
.plans h2{position:absolute;left:41px;top:56px;font-family:"Titillium Web",sans-serif;font-weight:400;font-size:23px;color:var(--white)}
.plans p{position:absolute;left:41px;top:98px;font-size:12px;line-height:24px;font-weight:600;color:var(--white)}
.plans a{position:absolute;left:41px;top:155px;font-size:12px;font-weight:600;color:#1a1a1a;text-decoration:none}
.plans .photo-frame{position:absolute;left:655px;top:22px;width:284px;height:182px;padding:5px;border:none}

.blog-img{top:1849px;width:321px;height:153px}
.blog-meta{top:2018px;font-size:11.5px;color:var(--muted)}
.blog-title{top:2040px;font-size:12.5px;font-weight:600;color:var(--ink)}

.tweet{left:805px;top:1800px;width:242px;text-align:center}
.tweet h2{font-size:22px}
.tweet-icon{width:26px;height:26px;border-radius:50%;background:#666;margin:30px auto 0}
.tweet-body{font-family:"Titillium Web",sans-serif;font-weight:600;color:#555;font-size:17px;line-height:21px;margin-top:6px}
.tweet-rule{width:67px;height:3px;background:#e24a4a;margin:19px auto 0}
.tweet-time{font-size:11.5px;color:var(--muted);margin-top:12px}

.quote{top:2170px;width:470px;font-size:12px;line-height:23px;color:var(--text)}
.quote p{padding-left:20px}
.quote cite{display:block;text-align:right;font-size:11.5px;font-weight:600;font-style:italic;color:var(--ink);padding-right:14px}
.quote-mark{position:absolute;font-family:Georgia,serif;font-size:34px;color:#555;line-height:1}

.site-footer{left:0;top:2284px;width:1200px;height:103px;background:var(--red);color:var(--white)}
.footer-links{position:absolute;left:115px;top:29px;font-size:12px}
.footer-links a{color:var(--white);text-decoration:none}
.copyright{position:absolute;left:115px;top:52px;font-size:12px}
.social{position:absolute;left:950px;top:21px;display:flex;gap:4px}
.social span{width:31px;height:31px;background:rgba(255,255,255,.85);border-radius:3px}
</style>
</head>
<body>

<div class="abs top-bar"></div>

<header>
  <div class="abs brand">
    <span class="brand-mark"></span>
    <span class="brand-text">Redline Builders, Inc.<small>General contractor and engineer</small></span>
  </div>
  <div class="abs search">
    <span>Search</span>
    <svg width="13" height="13" viewBox="0 0 14 14"><circle cx="6" cy="6" r="4.3" fill="none" stroke="#222" stroke-width="2"/><line x1="9.2" y1="9.2" x2="13" y2="13" stroke="#222" stroke-width="2.2"/></svg>
  </div>
  <nav class="abs main-nav">
    <a class="active" href="#">Home</a>
    <a href="#">About Us</a>
    <a href="#">Products</a>
    <a href="#">Customer Center</a>
    <a href="#">Resources</a>
    <a href="#">Contact Us</a>
  </nav>
</header>

<section class="abs slider">
  <div class="abs slide" role="img" aria-label="Two engineers in hard hats reviewing construction blueprints under a roof frame"></div>
  <div class="abs slider-arrow" style="left:29px">
    <svg width="32" height="32" viewBox="0 0 32 32"><path d="M18 10l-6 6 6 6" fill="none" stroke="#333" stroke-width="2.6"/></svg>
  </div>
  <div class="abs slider-arrow" style="left:900px">
    <svg width="32" height="32" viewBox="0 0 32 32"><path d="M14 10l6 6-6 6" fill="none" stroke="#333" stroke-width="2.6"/></svg>
  </div>
  <div class="abs slider-dots"><span class="on"></span><span></span><span></span></div>
</section>
<div class="abs slider-shadow"></div>

<section>
  <h1 class="abs section-title" style="left:115px;top:801px">Welcome To Our Company</h1>
  <p class="abs welcome-text">Lorem ipsum dolor sit amet, consectetuer adipiscing elit, sed diam nonummy nibh euismod tincidunt ut laoreet dolore magna aliquam erat volutpat. Ut wisi enim ad minim veniam, quis nostrud exerci tation ullamcorper suscipit lobortis nisl ut aliquip ex ea commodo consequat. Lorem ipsum dolor sit amet, consectetuer adipiscing elit, sed diam nonummy nibh euismod tincidunt ut laoreet dolore magna aliquam erat volutpat. Ut wisi enim ad minim veniam, quis nostrud exerci tation ullamcorper suscipit lobortis nisl ut aliquip ex ea commodo consequat. Lorem ipsum dolor sit amet, consectetuer adipiscing elit, sed diam nonummy nibh euismod tincidunt ut laoreet dolore magna aliquam erat volutpat. Ut wisi enim ad</p>
  <a class="abs read-more">Read more +</a>
  <div class="abs photo-frame" style="left:748px;top:793px;width:337px;height:253px">
    <div class="photo-fill" role="img" aria-label="Team of three engineers in yellow hard hats studying plans" style="background:linear-gradient(120deg,#c8ccd2,#8a8f98 45%,#d4c27a 70%,#a9aeb6)"></div>
  </div>
</section>

<section>
  <h2 class="abs section-title" style="left:115px;top:1093px">Services</h2>
  <article class="abs service-card" style="left:115px">
    <div class="service-img" role="img" aria-label="Commercial office tower against a blue sky" style="background:linear-gradient(180deg,#5f8fd0,#8d99a8 60%,#6b6f73)"></div>
    <h3>Commercial</h3>
    <p>Lorem ipsum dolor sit amet, consectetur adipisicing elit. Ullam voluptate, accusamus</p>
    <span class="more">-Readmore...</span>
  </article>
  <article class="abs service-card" style="left:363px">
    <div class="service-img" role="img" aria-label="Renovated interior with lit staircase" style="background:linear-gradient(180deg,#6a5e52,#c9bfae 55%,#3b332c)"></div>
    <h3>Tenant Improvement</h3>
    <p>Lorem ipsum dolor sit amet, consectetur adipisicing elit. Ullam voluptate, accusamus</p>
    <span class="more">-Readmore...</span>
  </article>
  <article class="abs service-card" style="left:610px">
    <div class="service-img" role="img" aria-label="Restaurant dining room with chandelier" style="background:linear-gradient(180deg,#5c4431,#8a5a3a 55%,#c9c3b6)"></div>
    <h3>Restaurants</h3>
    <p>Lorem ipsum dolor sit amet, consectetur adipisicing elit. Ullam voluptate, accusamus</p>
    <span class="more">-Readmore...</span>
  </article>
  <article class="abs service-card" style="left:858px">
    <div class="service-img" role="img" aria-label="Engineers in hard hats reviewing plans outside a building" style="background:linear-gradient(160deg,#8fa6c6,#dfe3e8 50%,#7b8899)"></div>
    <h3>Public Works</h3>
    <p>Lorem ipsum dolor sit amet, consectetur adipisicing elit. Ullam voluptate, accusamus</p>
    <span class="more">-Readmore...</span>
  </article>
</section>

<section class="abs plans">
  <h2>Make Plans</h2>
  <p>Please click on the link below to download instructions to assemble your knockdown kit.<br>If you still have questions feel free to call us at toll-free 800-555-0142.</p>
  <a href="#">Click here for Redline</a>
  <div class="photo-frame">
    <div class="photo-fill" role="img" aria-label="Workers in yellow hard hats marking up a blueprint" style="background:linear-gradient(135deg,#d9c24a,#e8e8ea 40%,#9fb0c8 75%,#dcdfe4)"></div>
  </div>
</section>

<section>
  <h2 class="abs section-title" style="left:115px;top:1796px;font-size:22px">From Our Blog</h2>
  <div class="abs blog-img" style="left:115px" role="img" aria-label="Hand tools and a yellow measuring rule on a wooden table" style="background:#8a6c4e"></div>
  <div class="abs blog-img" style="left:115px;background:linear-gradient(135deg,#7a5b3f,#b08a5e 50%,#c7a53a)"></div>
  <div class="abs blog-img" style="left:454px;background:linear-gradient(135deg,#f2d7c6,#e9b9a0 50%,#f4e2d6)" role="img" aria-label="Cupped hands holding a small model house"></div>
  <p class="abs blog-meta" style="left:115px">Aug 9, 2013&nbsp; 3 comments</p>
  <p class="abs blog-title" style="left:115px">Lorem ipsum dolor sit amet</p>
  <p class="abs blog-meta" style="left:454px">Aug 9, 2013&nbsp; 3 comments</p>
  <p class="abs blog-title" style="left:454px">Lorem ipsum dolor sit amet</p>
</section>

<aside class="abs tweet">
  <h2 class="section-title">Latest Tweet</h2>
  <div class="tweet-icon"></div>
  <p class="tweet-body">@buildwirethemes<br>Are you ready to sell some burgers? Our Food Truck theme is now equipped with ShopCart module!</p>
  <div class="tweet-rule"></div>
  <p class="tweet-time">about 12 days ago</p>
</aside>

<section>
  <h2 class="abs section-title" style="left:115px;top:2121px;font-size:25px">Testimonials</h2>
  <blockquote class="abs quote" style="left:115px">
    <span class="quote-mark" style="left:0;top:-6px">&ldquo;</span>
    <p>Lorem ipsum dolor sit amet, consectetuer adipiscing elit. Aenean commodo ligula eget dolor. Aenean massa. Cum sociis natoque penatibus et</p>
    <cite>-Martin Okelo, CEO</cite>
    <span class="quote-mark" style="right:-12px;top:54px">&rdquo;</span>
  </blockquote>
  <blockquote class="abs quote" style="left:600px">
    <span class="quote-mark" style="left:0;top:-6px">&ldquo;</span>
    <p>Lorem ipsum dolor sit amet, consectetuer adipiscing elit. Aenean commodo ligula eget dolor. Aenean massa. Cum sociis natoque penatibus et</p>
    <cite>-Martin Okelo, CEO</cite>
    <span class="quote-mark" style="right:-14px;top:54px">&rdquo;</span>
  </blockquote>
</section>

<footer class="abs site-footer">
  <nav class="footer-links"><a href="#">Home</a> &nbsp;|&nbsp; <a href="#">About Us</a> &nbsp;|&nbsp; <a href="#">Products</a> &nbsp;|&nbsp; <a href="#">Contact Us</a></nav>
  <p class="copyright">© 2014 Company Name &nbsp;All right reserved &nbsp;Term of Use</p>
  <div class="social"><span></span><span></span><span></span><span></span></div>
</footer>

</body>
</html>
```